Varnex Consulting Business card design.

See our website www.varnexconsulting.example which will give you a good idea of what we are about. The font is called 'Play'.

I'd like a standout business card in keeping with the themes and branding on the website

Target Market(s)

professionals. HR directors

Industry/Entity Type

Business

Contact Information for Business Card

Varnex Consulting PO Box 3172 Merrowdale NSW 2291 1300 485 193 Gavin Threlkeld Principal email: career@varnexconsulting.example ABN: 71203948865

Font styles to use
Other font styles liked:
• Play

Requirements
Must have
• Must have same design colours and branding as website.
• On back I'd prefer a list of the things we do which appears below the name at the header on the website

```html
<!DOCTYPE html>
<html lang="en">
<head>
<meta charset="utf-8">
<title>Varnex Consulting – Business Card</title>
<link href="https://fonts.googleapis.com/css2?family=Arimo:wght@400;700&display=swap" rel="stylesheet">
<style>
  :root {
    --page-bg: #e9e9ec;
    --navy-deep: #0a1624;
    --navy-mid: #13263a;
    --navy-light: #1f3a52;
    --brand-blue: #1f9be6;
    --ink: #1c2431;
    --ink-soft: #3a3f47;
    --paper: #ffffff;
    --paper-shade: #eeeeef;
    --muted-light: #c9d3dc;
  }
  * { box-sizing: border-box; margin: 0; padding: 0; }
  html, body { width: 1200px; height: 950px; overflow: hidden; }
  body {
    background: var(--page-bg);
    display: flex;
    flex-direction: column;
    align-items: center;
    justify-content: center;
    gap: 50px;
    font-family: "Arimo", sans-serif;
  }
  .card {
    position: relative;
    width: 700px;
    height: 400px;
    border-radius: 4px;
    box-shadow: 0 10px 30px rgba(0,0,0,0.18);
    overflow: hidden;
  }
  .company-name {
    font-family: "Arimo", sans-serif;
    font-weight: 400;
    letter-spacing: 1px;
    white-space: nowrap;
  }

  /* Back */
  .card-back {
    background: linear-gradient(120deg, var(--navy-deep) 0%, var(--navy-mid) 55%, var(--navy-light) 100%);
  }
  .card-back .company-name {
    position: absolute;
    left: 0; right: 0;
    top: 152px;
    text-align: center;
    font-size: 36px;
    color: var(--muted-light);
  }
  .services {
    position: absolute;
    right: 44px;
    top: 228px;
    font-size: 17px;
    color: var(--muted-light);
    letter-spacing: 0.5px;
    white-space: nowrap;
  }
  .services .divider { color: var(--brand-blue); margin: 0 8px; }

  /* Front */
  .card-front {
    background: linear-gradient(160deg, var(--paper) 40%, var(--paper-shade) 100%);
  }
  .side-bar {
    position: absolute;
    left: 0; top: 130px;
    width: 14px; height: 86px;
    background: var(--brand-blue);
  }
  .card-front .company-name {
    position: absolute;
    right: 44px;
    top: 66px;
    font-size: 40px;
    color: var(--navy-deep);
  }
  .holder {
    position: absolute;
    right: 44px;
    top: 150px;
    text-align: right;
  }
  .holder-name { font-weight: 700; font-size: 24px; color: var(--ink); }
  .holder-role { font-size: 19px; color: var(--brand-blue); margin-top: 4px; }
  .contact {
    position: absolute;
    left: 50px;
    top: 140px;
    font-size: 17px;
    line-height: 25px;
    color: var(--ink-soft);
    list-style: none;
  }
  .contact li { display: flex; align-items: center; gap: 8px; white-space: nowrap; }
  .contact .address { display: block; padding-left: 24px; }
  .contact svg { width: 16px; height: 16px; fill: var(--ink); flex: none; }
</style>
</head>
<body>

<section class="card card-back" aria-label="Card back">
  <div class="company-name">Varnex Consulting</div>
  <div class="services">Career Coaching<span class="divider">|</span>Leadership<span class="divider">|</span>Outplacement</div>
</section>

<section class="card card-front" aria-label="Card front">
  <div class="side-bar"></div>
  <div class="company-name">Varnex Consulting</div>
  <div class="holder">
    <div class="holder-name">Gavin Threlkeld</div>
    <div class="holder-role">Principal</div>
  </div>
  <ul class="contact">
    <li class="address">PO Box 3172 Merrowdale<br>NSW 2291</li>
    <li>
      <svg viewBox="0 0 16 16" aria-hidden="true"><path d="M2 5c0-2 2-3 6-3s6 1 6 3v1h-3V5H5v1H2z"/><path d="M4 7h8l2 6H2z"/><circle cx="8" cy="10" r="1.6" fill="#fff"/></svg>
      1300 485 193
    </li>
    <li>
      <svg viewBox="0 0 16 16" aria-hidden="true"><rect x="1" y="3" width="14" height="10" rx="1"/><path d="M1.5 3.5L8 9l6.5-5.5" stroke="#fff" stroke-width="1.3" fill="none"/></svg>
      career@varnexconsulting.example
    </li>
    <li>
      <svg viewBox="0 0 16 16" aria-hidden="true"><circle cx="8" cy="8" r="7"/><path d="M1 8h14M8 1c-3 3-3 11 0 14M8 1c3 3 3 11 0 14" stroke="#fff" stroke-width="1" fill="none"/></svg>
      www.varnexconsulting.example
    </li>
  </ul>
</section>

</body>
</html>
```